TERRAWISPA

We are a group of friends with a passion for ancestral knowledge of potions and medicinal formulas derived from nature. We specialise in medicinal mushrooms and adaptogens. We designed a few supplement formulas which we want to release to the market. Our team comes from biology and nutritional science background. Every product we launch will be clean in biodegradable packaging.
Our first product is a lab-tested grass-fed bovine collagen type I, II, and III mixed with organic lab-tested the most potent and bioavailable medicinal mushrooms on the market. This product will be in a pouch the print will be on the pouch or on a label, we don't know if it's possible to design a label that could be used on both? We don't know if we will be able to use organic labels yet due to the legislation changes in the UK. We are waiting for clarification.
The company is called Hollow Brook. We want to use forgotten ancestral knowledge of those potions and reintroduce them to the people. We would like our brand to look clean and friendly. A natural mix of modern and ancestral design.
Our logo and brand designs we like are attached. I have attached the source file of our logo if anyone thinks colours could be different we are open to ideas. I have also attached the visual design we were playing with on canva.com.

```html
<!DOCTYPE html>
<html lang="en">
<head>
<meta charset="utf-8">
<title>Terrawispa – Pouch and Label</title>
<link rel="stylesheet" href="https://fonts.googleapis.com/css2?family=Oswald:wght@300;400;700&family=Montserrat:ital,wght@0,500;0,700;0,800;0,900;1,500&family=Open+Sans:ital,wght@0,400;0,700;1,400&display=swap">
<style>
  :root {
    --orange: #e06a2c;
    --orange-deep: #c9531d;
    --orange-text: #c65a2a;
    --brush: #e39a3b;
    --ink: #222222;
    --paper: #f5f5f5;
    --stage: #ececed;
    --heading-grey: #cfcfcf;
  }
  * { box-sizing: border-box; margin: 0; padding: 0; }
  html, body { width: 855px; height: 1200px; overflow: hidden; }
  body { background: var(--stage); position: relative; font-family: "Open Sans", sans-serif; color: var(--ink); }

  .section-title {
    position: absolute; left: 0; width: 855px; text-align: center;
    font-family: "Montserrat", sans-serif; font-weight: 900; font-size: 44px;
    letter-spacing: 2px; color: var(--heading-grey);
  }
  .section-title--pouch { top: 18px; }
  .section-title--label { top: 588px; }

  .panel { position: absolute; width: 360px; height: 490px; background: var(--paper); overflow: hidden; }
  .panel--front { left: 45px; top: 78px; }
  .panel--back { left: 450px; top: 78px; }
  .panel--label { left: 45px; top: 650px; width: 765px; }

  .pattern-band {
    position: absolute; left: 0; top: 0; right: 0; height: 265px;
    background: radial-gradient(ellipse at 30% 35%, #e97a3c 0%, var(--orange) 55%, var(--orange-deep) 100%);
  }

  .face { position: absolute; top: 0; left: 50%; width: 360px; height: 490px; margin-left: -180px; }

  .brand-mark {
    position: absolute; left: 50%; width: 46px; height: 46px; margin-left: -23px;
    border-radius: 50%; background: #ffffff;
  }
  .brand-name {
    position: absolute; left: 0; right: 0; text-align: center;
    font-family: "Montserrat", sans-serif; font-weight: 700; font-size: 24px; color: #ffffff;
  }
  .face .brand-mark { top: 62px; }
  .face .brand-name { top: 120px; }

  .product-name {
    position: absolute; left: 0; right: 0; top: 186px; text-align: center;
    font-family: "Oswald", sans-serif; font-weight: 700; font-size: 72px; line-height: 80px;
    letter-spacing: -1px; color: #ffffff;
  }
  .subtitle {
    position: absolute; left: 0; right: 0; top: 282px; text-align: center;
    font-family: "Oswald", sans-serif; font-weight: 300; font-size: 26px; line-height: 30px;
    color: var(--orange-text);
  }
  .type-stroke {
    position: absolute; left: 50%; top: 352px; width: 262px; height: 28px; margin-left: -131px;
    background: var(--brush);
    clip-path: polygon(0 35%, 6% 10%, 20% 0, 80% 4%, 100% 12%, 96% 45%, 100% 80%, 85% 100%, 12% 94%, 3% 80%, 7% 55%);
    font-family: "Montserrat", sans-serif; font-weight: 800; font-size: 12.5px; line-height: 28px;
    color: #ffffff; text-align: center; letter-spacing: 0.5px;
  }
  .claims { position: absolute; left: 0; right: 0; top: 396px; display: flex; justify-content: center; gap: 14px; }
  .claim {
    width: 40px; height: 40px; border-radius: 50%; border: 3px solid var(--orange-text);
    box-shadow: inset 0 0 0 3px var(--paper), inset 0 0 0 4px var(--orange-text);
  }
  .pack-info { position: absolute; left: 0; right: 0; top: 446px; display: flex; justify-content: center; align-items: center; gap: 9px; }
  .pack-info__label {
    font-family: "Montserrat", sans-serif; font-weight: 800; font-size: 14px; line-height: 16px;
    color: var(--orange-text); border-bottom: 1px solid var(--orange-text);
  }
  .pack-info__weight { font-family: "Montserrat", sans-serif; font-weight: 800; font-size: 10px; margin-top: 3px; }
  .pack-info__divider { width: 1px; height: 32px; background: var(--ink); }
  .pack-info__count { font-family: "Montserrat", sans-serif; font-weight: 900; font-size: 28px; line-height: 24px; }
  .pack-info__unit { font-family: "Montserrat", sans-serif; font-weight: 700; font-size: 7px; }

  /* back of pouch */
  .panel--back .brand-mark { top: 45px; }
  .panel--back .brand-name { top: 100px; }
  .back-title {
    position: absolute; left: 0; right: 0; top: 146px; text-align: center;
    font-family: "Oswald", sans-serif; font-weight: 400; font-size: 20px; color: #ffffff;
  }
  .back-intro {
    position: absolute; left: 28px; right: 28px; top: 186px; text-align: center;
    font-style: italic; font-size: 6.4px; line-height: 9px; color: #ffffff;
  }
  .info-column { position: absolute; left: 22px; top: 276px; width: 152px; }
  .info-heading { font-weight: 700; font-size: 8px; color: var(--orange-text); margin-bottom: 2px; }
  .info-text { font-size: 6px; line-height: 8.2px; text-align: justify; margin-bottom: 9px; }
  .claims--small { position: static; justify-content: flex-start; gap: 8px; margin: 2px 0 14px; }
  .claims--small .claim { width: 22px; height: 22px; border-width: 2px; box-shadow: inset 0 0 0 2px var(--paper), inset 0 0 0 3px var(--orange-text); }
  .distributor { font-size: 5.8px; line-height: 8px; }

  .nutrition {
    position: absolute; left: 190px; top: 276px; width: 150px;
    border: 1px solid var(--ink); padding: 3px 4px; font-family: Arial, Helvetica, sans-serif;
  }
  .nutrition__title { font-weight: 700; font-size: 12px; letter-spacing: 0.6px; line-height: 13px; }
  .nutrition__serving { font-size: 4.6px; line-height: 5.6px; border-bottom: 3px solid var(--ink); padding-bottom: 2px; }
  .nutrition table { width: 100%; border-collapse: collapse; font-size: 4.6px; }
  .nutrition td { border-bottom: 0.5px solid var(--ink); padding: 0.8px 0; line-height: 5px; }
  .nutrition td.value { text-align: right; }
  .nutrition .indent { padding-left: 6px; }
  .nutrition .rule-thick td { border-bottom: 2px solid var(--ink); }
  .nutrition__note { font-size: 3.8px; line-height: 4.8px; margin-top: 2px; }
</style>
</head>
<body>

  <h2 class="section-title section-title--pouch">POUCH</h2>

  <article class="panel panel--front">
    <div class="pattern-band" role="img" aria-label="Orange band with faint line pattern of medicinal mushrooms"></div>
    <div class="face">
      <span class="brand-mark"></span>
      <p class="brand-name">Hollow Brook</p>
      <h1 class="product-name">TERRAWISPA</h1>
      <p class="subtitle">Collagen Peptides &amp;<br>Medicinal Mushrooms</p>
      <p class="type-stroke">TYPE I, II, III | UNFLAVOURED</p>
      <div class="claims"><span class="claim"></span><span class="claim"></span><span class="claim"></span><span class="claim"></span></div>
      <div class="pack-info">
        <div><p class="pack-info__label">FOOD SUPPLEMENT</p><p class="pack-info__weight">NET WT 360g (12.7OZ)</p></div>
        <span class="pack-info__divider"></span>
        <div><p class="pack-info__count">30</p><p class="pack-info__unit">SERVINGS</p></div>
      </div>
    </div>
  </article>

  <article class="panel panel--back">
    <div class="pattern-band" role="img" aria-label="Orange band with faint line pattern of medicinal mushrooms"></div>
    <span class="brand-mark"></span>
    <p class="brand-name">Hollow Brook</p>
    <h2 class="back-title">Collagen Peptides &amp; Medicinal Mushrooms</h2>
    <p class="back-intro">Lorem Ipsum is simply dummy text of the printing and typesetting industry. Lorem Ipsum has been the industry's standard dummy text ever since the 1500s, when an unknown printer took a galley of type and scrambled it to make a type specimen book. It has survived not only five centuries, but also the leap into electronic typesetting, remaining essentially unchanged.</p>

    <div class="info-column">
      <h3 class="info-heading">Why Collagen?</h3>
      <p class="info-text">Lorem Ipsum is simply dummy text of the printing and typesetting industry. Lorem Ipsum has been the industry's standard dummy text ever since the 1500s, when an unknown printer took a galley of type and scrambled it to make a type specimen book.</p>
      <h3 class="info-heading">How It's Made?</h3>
      <p class="info-text">Lorem Ipsum is simply dummy text of the printing and typesetting industry. Lorem Ipsum has been the industry's standard dummy text ever since the 1500s, when an unknown printer took a galley of type and scrambled it to make a type specimen book.</p>
      <div class="claims claims--small"><span class="claim"></span><span class="claim"></span><span class="claim"></span><span class="claim"></span></div>
      <h3 class="info-heading">Distributed by</h3>
      <p class="distributor">Hollow Brook<br>Lorem Ipsum is simply dummy text<br>of the printing and typesetting industry.<br>Lorem Ipsum has been the industry's</p>
    </div>

    <section class="nutrition">
      <p class="nutrition__title">Nutrition Facts</p>
      <p class="nutrition__serving">Serving Size 1/2 cup (114 gm) 1/2 cup<br>Serving Per Container 4</p>
      <table>
        <tr><td><b>Amount Per Serving</b></td><td class="value"></td></tr>
        <tr class="rule-thick"><td><b>Calories</b> 90</td><td class="value">Calories from Fat 30</td></tr>
        <tr><td></td><td class="value"><b>% Daily Values*</b></td></tr>
        <tr><td><b>Total Fat</b> 3g</td><td class="value"><b>5%</b></td></tr>
        <tr><td class="indent">Saturated Fat 0g</td><td class="value"><b>0%</b></td></tr>
        <tr><td class="indent">Trans Fat 0g</td><td class="value"></td></tr>
        <tr><td><b>Cholesterol</b> 0mg</td><td class="value"><b>0%</b></td></tr>
        <tr><td><b>Potassium</b> 20mg</td><td class="value"><b>1%</b></td></tr>
        <tr><td><b>Sodium</b> 300mg</td><td class="value"><b>13%</b></td></tr>
        <tr><td><b>Total Carbohydrate</b> 13g</td><td class="value"><b>4%</b></td></tr>
        <tr><td class="indent">Dietary Fiber 3g</td><td class="value"><b>12%</b></td></tr>
        <tr><td class="indent">Sugars 3g</td><td class="value"></td></tr>
        <tr class="rule-thick"><td><b>Protein</b> 3g</td><td class="value"><b>6%</b></td></tr>
      </table>
      <p class="nutrition__note">*Percent Daily Values are based on a 2,000 calorie diet. Your daily values may be higher or lower depending on your calorie needs.</p>
      <table>
        <tr><td>Total Fat</td><td>Less than</td><td>65g</td><td>80g</td></tr>
        <tr><td>Sat Fat</td><td>Less than</td><td>20g</td><td>25g</td></tr>
        <tr><td>Cholesterol</td><td>Less than</td><td>300mg</td><td>300mg</td></tr>
        <tr><td>Sodium</td><td>Less than</td><td>2400mg</td><td>2400mg</td></tr>
        <tr><td>Total Carbohydrate</td><td></td><td>300g</td><td>375g</td></tr>
        <tr><td>Dietary Fiber</td><td></td><td>25g</td><td>30g</td></tr>
      </table>
    </section>
  </article>

  <h2 class="section-title section-title--label">LABEL</h2>

  <article class="panel panel--label">
    <div class="pattern-band" role="img" aria-label="Orange band with faint line pattern of medicinal mushrooms"></div>
    <div class="face">
      <span class="brand-mark"></span>
      <p class="brand-name">Hollow Brook</p>
      <h1 class="product-name">TERRAWISPA</h1>
      <p class="subtitle">Collagen Peptides &amp;<br>Medicinal Mushrooms</p>
      <p class="type-stroke">TYPE I, II, III | UNFLAVOURED</p>
      <div class="claims"><span class="claim"></span><span class="claim"></span><span class="claim"></span><span class="claim"></span></div>
      <div class="pack-info">
        <div><p class="pack-info__label">FOOD SUPPLEMENT</p><p class="pack-info__weight">NET WT 360g (12.7OZ)</p></div>
        <span class="pack-info__divider"></span>
        <div><p class="pack-info__count">30</p><p class="pack-info__unit">SERVINGS</p></div>
      </div>
    </div>
  </article>

</body>
</html>
```